Interval Timer App

Need to have design for the attached wireframe. Similar app can be found here: https://shop.lumaverse.net/store/apps/details?id=cc.quillfern.pulseclock

```html
<!DOCTYPE html>
<html lang="en">
<head>
<meta charset="utf-8">
<title>Interval Timer</title>
<link rel="stylesheet" href="https://fonts.googleapis.com/css2?family=Noto+Sans:wght@400;500;700&display=swap">
<style>
  :root {
    --bg-top: #9af59a;
    --bg-bottom: #08e070;
    --blue: #1e82e0;
    --card: #ffffff;
    --ink: #222428;
    --track: #ffffff;
  }
  * { box-sizing: border-box; margin: 0; padding: 0; }
  html, body { width: 675px; height: 1200px; overflow: hidden; }
  body {
    font-family: "Noto Sans", sans-serif;
    background: linear-gradient(170deg, var(--bg-top) 0%, var(--bg-bottom) 100%);
    position: relative;
    color: var(--ink);
  }
  .back-button { position: absolute; left: 28px; top: 36px; width: 32px; height: 40px; }
  .set-progress { position: absolute; left: 195px; top: 166px; width: 287px; text-align: center; }
  .set-label { font-size: 22px; font-weight: 500; letter-spacing: 0.5px; }
  .progress-track { position: relative; height: 5px; background: var(--track); margin-top: 18px; border-radius: 3px; }
  .progress-fill { position: absolute; left: 0; top: 0; height: 100%; width: 177px; background: var(--blue); border-radius: 3px; }
  .progress-knob {
    position: absolute; left: 166px; top: -9px; width: 23px; height: 23px;
    border-radius: 50%; background: #fff; border: 4px solid var(--blue);
  }
  .timer-card {
    position: absolute; left: 30px; top: 281px; width: 615px; height: 638px;
    background: var(--card); border-radius: 16px;
  }
  .phase-title { text-align: center; margin-top: 46px; font-size: 42px; font-weight: 500; }
  .countdown { text-align: center; color: var(--blue); font-size: 94px; font-weight: 500; line-height: 1; margin-top: 22px; }
  .set-list { list-style: none; margin: 30px 20px 0 19px; }
  .set-row { display: flex; justify-content: space-between; align-items: center; height: 55px; }
  .set-name { font-size: 33px; }
  .set-time { font-size: 26px; font-weight: 700; color: var(--blue); }
  .round-button {
    position: absolute; top: 511px; width: 103px; height: 103px; border-radius: 50%;
    background: #fff; box-shadow: 0 2px 8px rgba(0,0,0,0.18);
    display: flex; align-items: center; justify-content: center;
  }
  .reset-button { left: 19px; }
  .done-button { right: 19px; }
</style>
</head>
<body>
  <svg class="back-button" viewBox="0 0 32 40" aria-label="Back">
    <polyline points="22,6 8,20 22,34" fill="none" stroke="var(--blue)" stroke-width="4" stroke-linecap="round" stroke-linejoin="round"/>
  </svg>

  <div class="set-progress">
    <div class="set-label">SET 2</div>
    <div class="progress-track">
      <div class="progress-fill"></div>
      <div class="progress-knob"></div>
    </div>
  </div>

  <main class="timer-card">
    <h1 class="phase-title">Work time!</h1>
    <div class="countdown">2:45</div>
    <ul class="set-list">
      <li class="set-row"><span class="set-name">Set 1</span><span class="set-time">2:30</span></li>
      <li class="set-row"><span class="set-name">Set 2</span><span class="set-time">2:45</span></li>
    </ul>

    <div class="round-button reset-button" aria-label="Restart">
      <svg width="52" height="56" viewBox="0 0 52 56">
        <path d="M18 12 A20 20 0 1 0 34 12" fill="none" stroke="var(--blue)" stroke-width="4" stroke-linecap="round"/>
        <polyline points="8,8 18,12 14,22" fill="none" stroke="var(--blue)" stroke-width="4" stroke-linecap="round" stroke-linejoin="round"/>
      </svg>
    </div>
    <div class="round-button done-button" aria-label="Complete">
      <svg width="50" height="36" viewBox="0 0 50 36">
        <polyline points="6,20 18,28 44,10" fill="none" stroke="var(--blue)" stroke-width="5" stroke-linecap="round" stroke-linejoin="round"/>
      </svg>
    </div>
  </main>
</body>
</html>
```